Harrow Tavern & Grille Menu Makeover

I am looking for a professional look to update our current menu. We are an independently owned sports bar and grill. Up to this point, I have done all of my own graphic designing. I am looking for something classy/family oriented. We are a very family friendly sports bar that offers a wide variety of menu options. Our website is www.harrowtavernco.example. This may help you get more of a feel for what type of place we are and what we offer. Our menu is listed on the website. My current menu is 8.5x14 inserts that feature a cover page, 4 inside pages and a back page. I would like something a little more condensed than this. Possibly a large tri-fold menu? I am open to all new ideas. I do have some pictures on my menu now, and would like to continue using a few pictures to feature some of my items. I would like something that is in a format that gives me the option to change items and prices on my own in the future. I would also like it to feature, or inform my patrons about our technology that we offer. We offer online ordering and we are a "verified venue" with Brewvoke.( a social site for craft beer lovers).

Industry/Entity Type

Sports Bar

Requirements
Nice to have
• Nice to have some pictures, but does not have to. We do feature 9 different beers on tap. A lot of them are local craft beers from the state of Kansas. Not sure if that is something we can feature, but it is a nice talking point. All of our tables and bar are hand built. With a rich mahogany finish on all of our woodwork, some type of "woodgrain" look into the menu would be nice.

```html
<!DOCTYPE html>
<html lang="en">
<head>
<meta charset="utf-8">
<title>Harrow Tavern &amp; Grille — Pasta, Mexican &amp; Sides</title>
<link href="https://fonts.googleapis.com/css2?family=Libre+Baskerville:wght@700&family=Oswald:wght@300;400&family=Montserrat:wght@700&display=swap" rel="stylesheet">
<style>
  :root{
    --wood-dark:#3a140a;
    --wood-mid:#6b2a14;
    --wood-light:#8a3a1c;
    --paper:#d9c19a;
    --paper-light:#e6d3b0;
    --paper-edge:#a9875a;
    --ink:#231a12;
    --ink-soft:#3b2e22;
    --note:#f4ede2;
  }
  *{margin:0;padding:0;box-sizing:border-box}
  html,body{width:850px;height:1200px;overflow:hidden}
  body{
    position:relative;
    background:
      repeating-linear-gradient(90deg, rgba(0,0,0,.10) 0 3px, transparent 3px 11px, rgba(255,160,110,.05) 11px 14px, transparent 14px 29px),
      linear-gradient(90deg, var(--wood-dark), var(--wood-mid) 25%, var(--wood-light) 50%, var(--wood-mid) 75%, var(--wood-dark));
    color:var(--ink);
    font-family:'Oswald',sans-serif;
  }
  .sheet{position:absolute;left:0;top:0;width:850px;height:1200px}
  .section-title{
    position:absolute;font-family:'Libre Baskerville',serif;font-weight:700;
    font-size:33px;letter-spacing:.5px;color:var(--ink);line-height:1;
  }
  .item{position:absolute;width:320px}
  .item-name{font-weight:400;font-size:16px;line-height:1.05;text-transform:uppercase;color:var(--ink)}
  .item-desc{font-weight:300;font-size:9.2px;line-height:1.3;text-transform:uppercase;color:var(--ink-soft);margin-top:1px}
  .item-price{font-family:'Montserrat',sans-serif;font-weight:700;font-size:7.4px;letter-spacing:.6px;color:var(--ink-soft)}
  .side{position:absolute}
  .divider{position:absolute;height:1.5px;background:var(--ink);opacity:.8}
  .dish-photo{position:absolute;left:624px;top:234px;width:133px;height:133px;border-radius:50%;
    background:radial-gradient(circle at 45% 40%, #e8c34a, #c98f2c 55%, #7a3f16);border:2px solid #1a120b}
  .footer{position:absolute;top:1023px;left:190px;display:flex;align-items:center;
    font-family:'Montserrat',sans-serif;font-weight:700;font-size:8px;letter-spacing:.8px;text-transform:uppercase;color:var(--ink)}
  .footer .mark{width:17px;height:17px;background:var(--ink);margin-right:10px}
  .footer .link{margin-right:26px}
  .note{position:absolute;top:1152px;left:0;width:850px;text-align:center;
    font-family:'Montserrat',sans-serif;font-weight:700;font-size:7px;letter-spacing:.5px;text-transform:uppercase;color:var(--note)}
</style>
</head>
<body>
<svg class="sheet" viewBox="0 0 850 1200" aria-hidden="true">
  <defs>
    <radialGradient id="paperTone" cx="50%" cy="45%" r="65%">
      <stop offset="0" stop-color="#e6d3b0"/>
      <stop offset=".7" stop-color="#d3b88c"/>
      <stop offset="1" stop-color="#a9875a"/>
    </radialGradient>
  </defs>
  <polygon fill="url(#paperTone)" points="
    70,90 110,80 150,88 200,78 260,86 330,80 390,88 460,79 520,86 590,80 650,88 710,82 760,86 790,78 800,110 795,150 804,200 796,260 806,330 797,400 805,470 796,540 804,610 797,680 806,750 798,820 805,890 796,960 804,1020 790,1060 760,1072 700,1064 640,1074 580,1066 520,1074 450,1065 380,1073 310,1065 250,1074 190,1066 130,1072 80,1064 52,1050 58,1000 48,940 56,870 46,800 55,730 47,660 56,590 46,520 55,450 47,380 56,310 46,240 55,170 48,120"/>
</svg>

<h2 class="section-title" style="left:94px;top:150px">PASTA</h2>
<div class="item" style="left:98px;top:194px">
  <div class="item-name">Lasagna</div>
  <div class="item-desc">Harrow famous homemade lasagna!</div>
  <div class="item-price">SMALL 7.99 / LARGE 9.99</div>
</div>
<div class="item" style="left:98px;top:238px">
  <div class="item-name">Italian Spaghetti &amp; Meatballs</div>
  <div class="item-desc">This classic is topped with shredded parmesan cheese.</div>
  <div class="item-price">SMALL 6.99 / LARGE 8.99</div>
</div>
<div class="item" style="left:427px;top:194px;width:330px">
  <div class="item-name">Fettuccini Alfredo</div>
  <div class="item-desc">Fettuccini topped with creamy alfredo and blended Normandy vegetables served with your choice of chicken or grilled shrimp.</div>
  <div class="item-price">SMALL 7.99 / LARGE 9.99</div>
</div>
<div class="item" style="left:427px;top:250px;width:190px">
  <div class="item-name">Chicken Parmesan</div>
  <div class="item-desc">Tender grilled chicken breast topped with marinara sauce and parmesan cheese served on a bed of spaghetti</div>
  <div class="item-price">SMALL 7.99 / LARGE 9.99</div>
</div>
<div class="dish-photo" role="img" aria-label="Photo of a slice of baked lasagna with melted cheese"></div>
<div class="divider" style="left:204px;top:347px;width:436px"></div>

<h2 class="section-title" style="left:88px;top:372px">MEXICAN</h2>
<div class="item" style="left:94px;top:417px">
  <div class="item-name">Taco Bowl</div>
  <div class="item-desc">Your choice of chicken or beef in a fried 12 inch tortilla bowl, topped with lettuce, jack and cheddar cheese, tomatoes and sour cream.</div>
  <div class="item-price">8.99</div>
</div>
<div class="item" style="left:94px;top:473px">
  <div class="item-name">Six Pack Tacos</div>
  <div class="item-desc">Six crispy tacos stuffed with beef, cheese, lettuce and tomatoes.</div>
  <div class="item-price">8.99</div>
</div>
<div class="item" style="left:94px;top:517px">
  <div class="item-name">Chimichanga</div>
  <div class="item-desc">A 12 inch flour tortilla deep fried and stuffed with your choice of chicken or beef and jack and cheddar cheese. Smothered in melted jack cheese, lettuce, and tomatoes.</div>
  <div class="item-price">8.99</div>
</div>
<div class="item" style="left:422px;top:417px;width:335px">
  <div class="item-name">Southwest Chicken Sancho</div>
  <div class="item-desc">A bend of grilled chicken, cheese, lettuce, and salsa, wrapped in a tortilla and smothered with creamy alfredo sauce, jack and cheddar cheese and tomatoes.</div>
  <div class="item-price">8.99</div>
</div>
<div class="item" style="left:422px;top:473px;width:335px">
  <div class="item-name">Loaded Chicken Quesadilla</div>
  <div class="item-desc">12 inch flour tortilla loaded with grilled chicken, barbecue sauce, crisp bacon and grilled onions and peppers.</div>
  <div class="item-price">9.99</div>
</div>
<div class="divider" style="left:204px;top:610px;width:436px"></div>

<h2 class="section-title" style="left:88px;top:642px">SIDES</h2>
<div class="side" style="left:94px;top:686px"><div class="item-name">French Fries</div><div class="item-price">2.00</div></div>
<div class="side" style="left:94px;top:726px"><div class="item-name">Curly Fries</div><div class="item-price">2.00</div></div>
<div class="side" style="left:94px;top:766px"><div class="item-name">Mashed Potatoes</div><div class="item-price">2.00</div></div>
<div class="side" style="left:94px;top:806px"><div class="item-name">Steamed Vegetables</div><div class="item-price">2.50</div></div>
<div class="side" style="left:94px;top:846px"><div class="item-name">Loaded Baked Potato</div><div class="item-price">2.50</div></div>
<div class="side" style="left:94px;top:886px"><div class="item-name">Onion Rings</div><div class="item-price">2.00</div></div>
<div class="side" style="left:94px;top:926px"><div class="item-name">Fruit Dish</div><div class="item-price">2.00</div></div>
<div class="side" style="left:422px;top:686px"><div class="item-name">Cole Slaw</div><div class="item-price">2.00</div></div>
<div class="side" style="left:422px;top:726px"><div class="item-name">Dinner Salad</div><div class="item-price">2.99</div></div>
<div class="side" style="left:422px;top:766px"><div class="item-name">Grilled Shrimp Skewer</div><div class="item-price">2.00</div></div>
<div class="side" style="left:422px;top:806px"><div class="item-name">Sweet Potato Fries</div><div class="item-price">2.99</div></div>
<div class="side" style="left:422px;top:846px"><div class="item-name">Potato Chips</div><div class="item-price">2.00</div></div>
<div class="side" style="left:422px;top:886px"><div class="item-name">Cottage Cheese</div><div class="item-price">2.00</div></div>
<div class="side" style="left:422px;top:926px"><div class="item-name">Macaroni &amp; Cheese</div><div class="item-price">4.00</div></div>

<div class="footer">
  <span class="mark"></span><span class="link">harrowtavernandgrille</span>
  <span class="mark"></span><span class="link">harrowtavernco.example</span>
  <span class="link">Brewvoke</span>
</div>

<p class="note">When splitting a large portion, you will be charged the price of a small portion if a small portion is offered</p>
</body>
</html>
```